We need a new business card that reflects who we are. Professional, classy, modern, and service ori

We need a business card design for a window coverings design company in Kansas City called Bright Lane Interiors. We offer professional, modern, and high quality window covering products. We are looking to portray an image of a big, national franchise. We are a 5 location (with showrooms) business with 10 professional designers and 4 professional installers. These cards will be used with Thank you cards, given to realtors, and asked for referrals with.

Target Market(s)

Kansas City

Industry/Entity Type

Business

Contact Information for Business Card

We would like our card to look clean and simple on the front, featuring our logo and Marlow Fenwick's. Our designers' phone numbers and emails should be displayed as well as their title.

Font styles to use
Sans Serif

Colors

Designer to choose colors to be used in the design.

Requirements
Must have
• Front - Logos, name, phone number, email address
• Back - Showroom locations, social media? Appt date/time?
Nice to have
• I would like a clean and modern look (not contemporary. I like a white background, but I am open to ideas. Looking for a "National chain" look for a small business.
Should not have
• Too much busyness.

```html
<!DOCTYPE html>
<html lang="en">
<head>
<meta charset="utf-8">
<title>Bright Lane Interiors – Business Card</title>
<link rel="stylesheet" href="https://fonts.googleapis.com/css2?family=Open+Sans:wght@400;600;700&family=Tinos:wght@400;700&display=swap">
<style>
  :root {
    --page-bg: #2b2b2b;
    --card-white: #ffffff;
    --card-black: #0b0b0b;
    --brand-red: #d9464f;
    --ink: #1c1c1c;
    --ink-soft: #555a60;
    --partner-badge: #f0903a;
    --rule: #9a9a9a;
    --white: #ffffff;
  }
  * { box-sizing: border-box; margin: 0; padding: 0; }
  html, body { width: 1200px; height: 900px; overflow: hidden; }
  body {
    background: var(--page-bg);
    font-family: "Open Sans", sans-serif;
    display: flex;
    flex-direction: column;
    align-items: center;
    justify-content: center;
    gap: 30px;
  }
  .card {
    width: 700px;
    height: 400px;
    position: relative;
    overflow: hidden;
    background: var(--card-white);
  }

  /* ---------- Appointment side ---------- */
  .brand-mark {
    position: absolute;
    top: 40px;
    right: 60px;
    display: flex;
    align-items: center;
    gap: 10px;
    font-family: "Tinos", serif;
    font-weight: 700;
    font-size: 22px;
    color: var(--brand-red);
    white-space: nowrap;
  }
  .brand-mark .square { width: 26px; height: 26px; background: var(--brand-red); }
  .appt-title {
    position: absolute;
    top: 140px;
    left: 50px;
    font-weight: 700;
    font-size: 20px;
    color: var(--brand-red);
  }
  .field {
    position: absolute;
    display: flex;
    align-items: flex-end;
    font-weight: 600;
    font-size: 15px;
    color: var(--brand-red);
    white-space: nowrap;
  }
  .field .line {
    flex: 1;
    border-bottom: 1px dotted var(--rule);
    margin: 0 8px;
    height: 16px;
  }
  .field .suffix { font-size: 10px; font-weight: 600; }
  .field-name { top: 184px; left: 50px; width: 370px; }
  .field-time { top: 184px; left: 430px; width: 210px; }
  .field-date { top: 224px; left: 50px; width: 370px; }
  .partner {
    position: absolute;
    top: 226px;
    right: 60px;
    display: flex;
    align-items: center;
    gap: 8px;
    font-weight: 700;
    font-size: 14px;
    color: var(--ink-soft);
    white-space: nowrap;
  }
  .partner .badge { width: 18px; height: 18px; border-radius: 50%; background: var(--partner-badge); }
  .locations {
    position: absolute;
    left: 0;
    right: 0;
    top: 280px;
    height: 38px;
    background: var(--brand-red);
    color: var(--white);
    font-weight: 700;
    font-size: 14px;
    letter-spacing: 0.3px;
    display: flex;
    align-items: center;
    padding-left: 50px;
    white-space: nowrap;
  }
  .social {
    position: absolute;
    left: 50px;
    top: 336px;
    display: flex;
    gap: 8px;
  }
  .social span { width: 22px; height: 22px; border-radius: 50%; background: var(--brand-red); }

  /* ---------- Contact side ---------- */
  .card-front { display: flex; }
  .front-logo {
    width: 50%;
    background: var(--card-white);
    display: flex;
    flex-direction: column;
    justify-content: center;
    align-items: center;
    text-align: center;
    padding: 0 30px;
  }
  .front-logo .square { width: 60px; height: 60px; background: var(--brand-red); }
  .front-logo .brand-name {
    margin-top: 14px;
    font-family: "Tinos", serif;
    font-weight: 700;
    font-size: 28px;
    color: var(--brand-red);
    white-space: nowrap;
  }
  .front-logo .tagline {
    margin-top: 6px;
    font-family: "Tinos", serif;
    font-size: 15px;
    color: var(--ink);
    white-space: nowrap;
  }
  .front-contact {
    width: 50%;
    background: var(--card-black);
    color: var(--white);
    font-family: "Tinos", serif;
    padding: 110px 0 0 40px;
  }
  .designer-name { font-size: 28px; font-weight: 400; color: var(--brand-red); letter-spacing: 0.5px; }
  .designer-title { font-size: 18px; margin-top: 2px; letter-spacing: 0.5px; }
  .contact-list { list-style: none; margin-top: 34px; }
  .contact-list li {
    display: flex;
    align-items: center;
    gap: 12px;
    font-size: 16px;
    margin-bottom: 8px;
    white-space: nowrap;
  }
  .contact-list svg { width: 14px; height: 14px; flex: none; }
</style>
</head>
<body>

  <section class="card card-appointment">
    <div class="brand-mark"><span class="square"></span>Bright Lane Interiors</div>
    <h2 class="appt-title">Next Appointment</h2>
    <div class="field field-name">Name :<span class="line"></span></div>
    <div class="field field-time">Time :<span class="line"></span><span class="suffix">AM/PM</span></div>
    <div class="field field-date">Date :<span class="line"></span></div>
    <div class="partner"><span class="badge"></span>Marlow Fenwick Gallery</div>
    <div class="locations">NORTHGATE | RIVER BEND | MAPLE HILL | WESTFIELD | CEDAR POINT</div>
    <div class="social" aria-label="Social media links"><span></span><span></span><span></span><span></span></div>
  </section>

  <section class="card card-front">
    <div class="front-logo">
      <span class="square"></span>
      <p class="brand-name">Bright Lane Interiors</p>
      <p class="tagline">Blinds, Shades, Shutters, Draperies &amp; Decor</p>
    </div>
    <div class="front-contact">
      <h1 class="designer-name">EVAN CALDER</h1>
      <p class="designer-title">DESIGNER</p>
      <ul class="contact-list">
        <li>
          <svg viewBox="0 0 24 24"><path fill="#d9464f" d="M6.6 10.8a15.1 15.1 0 0 0 6.6 6.6l2.2-2.2a1 1 0 0 1 1-.25 11.4 11.4 0 0 0 3.6.57 1 1 0 0 1 1 1V20a1 1 0 0 1-1 1A17 17 0 0 1 3 4a1 1 0 0 1 1-1h3.5a1 1 0 0 1 1 1c0 1.25.2 2.45.57 3.57a1 1 0 0 1-.25 1z"/></svg>
          913.555.0148
        </li>
        <li>
          <svg viewBox="0 0 24 24"><rect x="2" y="5" width="20" height="14" rx="1" fill="#d9464f"/><path d="M3 6l9 7 9-7" stroke="#0b0b0b" stroke-width="2" fill="none"/></svg>
          info@brightlaneinteriors.com
        </li>
        <li>
          <svg viewBox="0 0 24 24"><circle cx="12" cy="12" r="10" fill="#d9464f"/><path d="M2 12h20M12 2c3 3 3 17 0 20M12 2c-3 3-3 17 0 20" stroke="#0b0b0b" stroke-width="1.6" fill="none"/></svg>
          brightlaneinteriors.com
        </li>
      </ul>
    </div>
  </section>

</body>
</html>
```